Business Card Design for Marketing Firm

Looking for business card design for higher end marketing firm. Clean but impressionable/trendy. We are a marketing firm that represents manufacturers in the foodservice equipment and supply industry. Our customers are end users such has hotels, restaurants, country clubs, convention centers and casinos as well as distributors of restaurants supplies and equipment, and manufacturers of foodservice equipment and supplies.
Target Market(s)
Hotels, Restaurants, Supply & Equipment Distributors, Foodservice Manufacturers
Industry/Entity Type
Foodservice/Hospitality
Contact Information for Business Card
Name, Title, Contact Number, Email, Website, Social Media, Address
Requirements
Must have
- Clean & Simple but Serious and Impressionable

```html
<!DOCTYPE html>
<html lang="en">
<head>
<meta charset="utf-8">
<title>Harbor Service Reps – Business Card</title>
<link href="https://fonts.googleapis.com/css2?family=Montserrat:wght@400;600;700&display=swap" rel="stylesheet">
<style>
  :root {
    --navy: #2d2f66;
    --ink: #2b2b3a;
    --paper: #ffffff;
    --grey-band: #b9b9bc;
    --backdrop: #9c8868;
  }
  * { box-sizing: border-box; margin: 0; padding: 0; }
  html, body { width: 900px; height: 1200px; overflow: hidden; }
  body {
    background: var(--backdrop);
    font-family: "Montserrat", Arial, sans-serif;
    position: relative;
  }
  .card {
    position: absolute;
    left: 80px;
    width: 742px;
    height: 440px;
    border-radius: 30px;
    overflow: hidden;
    box-shadow: 0 6px 14px rgba(0,0,0,0.35);
  }
  .card--front { top: 132px; background: var(--paper); }
  .card--back { top: 638px; background: var(--navy); }

  .brand {
    position: absolute;
    display: flex;
    align-items: center;
    gap: 12px;
    font-weight: 600;
    letter-spacing: 1.5px;
    text-transform: uppercase;
    white-space: nowrap;
  }
  .brand__dot { border-radius: 50%; flex: none; }
  .card--front .brand { left: 40px; top: 138px; font-size: 25px; color: var(--navy); }
  .card--front .brand__dot { width: 14px; height: 14px; background: var(--navy); }
  .card--back .brand {
    left: 0; right: 0; top: 222px; justify-content: center;
    font-size: 38px; color: var(--paper);
  }
  .card--back .brand__dot { width: 20px; height: 20px; background: var(--paper); }

  .person { position: absolute; right: 44px; top: 278px; text-align: right; }
  .person__name { font-size: 27px; font-weight: 700; color: var(--navy); line-height: 1.2; }
  .person__title { font-size: 15.5px; color: var(--ink); margin-top: 6px; }
  .divider {
    position: absolute; left: 42px; top: 324px; width: 506px; height: 1.5px;
    background: var(--ink);
  }
  .contacts { position: absolute; left: 38px; top: 340px; list-style: none; }
  .contacts li {
    display: flex; align-items: center; gap: 10px;
    font-size: 16px; color: var(--ink); height: 24px;
  }
  .contacts svg { width: 15px; height: 15px; fill: var(--ink); flex: none; }

  .footer-band { position: absolute; left: 0; bottom: 0; width: 742px; height: 40px; }
  .address {
    position: absolute; left: 357px; bottom: 8px;
    font-size: 15.5px; color: var(--paper); white-space: nowrap;
  }
</style>
</head>
<body>
  <section class="card card--front">
    <div class="brand"><span class="brand__dot"></span>Harbor Service Reps</div>

    <div class="person">
      <div class="person__name">Daniel Reyes</div>
      <div class="person__title">CEO &amp; Founder</div>
    </div>
    <div class="divider"></div>

    <ul class="contacts">
      <li>
        <svg viewBox="0 0 16 16" aria-hidden="true"><path d="M3.6 1.5l2.3 2.6-1.2 1.6c.9 2 2.4 3.5 4.5 4.5l1.6-1.2 2.6 2.3-1.4 2.3C7.4 13.4 2.6 8.6 1.3 2.9z"/></svg>
        (555) 014-2837
      </li>
      <li>
        <svg viewBox="0 0 16 16" aria-hidden="true"><path d="M1 3h14v1.2L8 8.8 1 4.2zM1 5.8l7 4.6 7-4.6V13H1z"/></svg>
        info@harborservicereps.com
      </li>
      <li>
        <svg viewBox="0 0 16 16" aria-hidden="true"><circle cx="8" cy="8" r="7"/><path d="M5 4.5c1.5.3 2 1.5 1.2 2.6-.8 1 .6 2 1.8 1.6 1.1-.4 1.3 1.6.3 2.6M10 2.5c.2 1.4 1.4 1.7 2.8 1.5" stroke="#fff" stroke-width="1.2" fill="none"/></svg>
        www.harborservicereps.com
      </li>
    </ul>

    <svg class="footer-band" viewBox="0 0 742 40" aria-hidden="true">
      <polygon points="0,25 332,25 320,40 0,40" fill="var(--grey-band)"/>
      <polygon points="353,0 742,0 742,40 318,40" fill="var(--navy)"/>
    </svg>
    <div class="address">418 Marlow Avenue, Suite 620, Bayview, CA 90210</div>
  </section>

  <section class="card card--back">
    <div class="brand"><span class="brand__dot"></span>Harbor Service Reps</div>
  </section>
</body>
</html>
```